Lanternfield Drinks business cards

We need a business card design for our new logo. The company is modern, progressive, professional, yet approachable. The key products are ready to drink bottles and cans of coffee based beverages.
These cards will be a critical part of the first impression made by our sales organization, business development team, and all external facing personnel.
Card can be a vertical or horizontal orientation.

Target Market(s)

Customers, suppliers, business partners

Industry/Entity Type

Business

Contact Information for Business Card

Business cards should feature Company Name and Logo.

Font styles to use
Serif

Colors

Designer to choose colors to be used in the design.

Requirements
Must have
• Strong readability of Name, phone #, mobile number and email address.
• Job title, website url, Street Address, and other details can be secondary level readability.
Nice to have
• High impact, simplistic quality design.
• Ok to utilize the 'H in the box' separate from the company name

```html
<!DOCTYPE html>
<html lang="en">
<head>
<meta charset="utf-8">
<title>Lanternfield Drinks – Business Cards</title>
<link rel="stylesheet" href="https://fonts.googleapis.com/css2?family=Cinzel:wght@400;700&family=PT+Sans:wght@400;700&display=swap">
<style>
  :root {
    --backdrop: #3a3a3a;
    --card-front: #ececec;
    --brand-orange: #f05a28;
    --brand-amber: #f7941d;
    --text-dark: #3c3c3c;
    --rule-tan: #e2c49a;
    --white: #ffffff;
  }
  * { margin: 0; padding: 0; box-sizing: border-box; }
  html, body { width: 1200px; height: 900px; overflow: hidden; }
  body { background: var(--backdrop); position: relative; font-family: "PT Sans", sans-serif; }

  .card { position: absolute; top: 170px; width: 347px; height: 561px; }
  .card--front { left: 259px; background: var(--card-front); text-align: center; }
  .card--back {
    left: 631px;
    background: linear-gradient(160deg, var(--brand-orange) 0%, var(--brand-amber) 45%, var(--brand-amber) 70%, var(--brand-orange) 100%);
    text-align: center;
  }

  .brand-square {
    position: absolute; left: 132px; top: 90px;
    width: 84px; height: 84px; background: var(--brand-orange);
  }
  .brand-name {
    position: absolute; left: 0; width: 100%;
    font-family: "Cinzel", serif; font-weight: 700;
    color: var(--brand-orange); line-height: 1.05;
  }
  .card--front .brand-name { top: 186px; font-size: 29px; }
  .card--back .brand-name { top: 250px; font-size: 34px; color: var(--white); }

  .person-name {
    position: absolute; top: 318px; left: 0; width: 100%;
    font-family: "Cinzel", serif; font-size: 22px; color: var(--brand-orange); letter-spacing: 0.5px;
  }
  .person-title {
    position: absolute; top: 345px; left: 0; width: 100%;
    font-size: 15px; color: var(--text-dark);
  }

  .divider {
    position: absolute; left: 92px; width: 163px; height: 16px;
    display: flex; align-items: center; justify-content: center; gap: 5px;
  }
  .divider::before, .divider::after {
    content: ""; flex: 1; height: 1px; background: var(--rule-tan);
  }
  .divider--contact { top: 379px; }
  .divider--address { top: 465px; }
  .icon-box {
    width: 17px; height: 16px; background: var(--brand-orange);
    display: flex; align-items: center; justify-content: center;
  }
  .icon-box svg { width: 11px; height: 11px; fill: var(--white); }

  .contact-lines {
    position: absolute; top: 400px; left: 0; width: 100%;
    font-size: 15px; line-height: 20px; color: var(--text-dark);
  }
  .address-lines {
    position: absolute; top: 486px; left: 0; width: 100%;
    font-size: 15px; line-height: 21px; color: var(--text-dark);
  }

  .website {
    position: absolute; top: 502px; left: 0; width: 100%;
    font-size: 17px; font-weight: 700; letter-spacing: 1px; color: var(--white);
  }
</style>
</head>
<body>
  <section class="card card--front">
    <div class="brand-square"></div>
    <div class="brand-name">LANTERNFIELD<br>DRINKS</div>

    <div class="person-name">Daniel Harper</div>
    <div class="person-title">Managing Director</div>

    <div class="divider divider--contact">
      <span class="icon-box"><svg viewBox="0 0 12 12"><path d="M1 4c0-1.5 2-2.5 5-2.5S11 2.5 11 4v1H8.5V3.8h-5V5H1zM2.5 6h7l1 4.5h-9z"/></svg></span>
      <span class="icon-box"><svg viewBox="0 0 12 12"><path d="M3 0h6v12H3zM4 1.5v8h4v-8z"/></svg></span>
      <span class="icon-box"><svg viewBox="0 0 12 12"><path d="M0 2h12v8H0zM1 3l5 4 5-4v-.2H1z"/></svg></span>
    </div>
    <div class="contact-lines">
      044-210 387 654<br>
      044-210 387 655<br>
      info@lanternfield.com
    </div>

    <div class="divider divider--address">
      <span class="icon-box"><svg viewBox="0 0 12 12"><path d="M6 0a4 4 0 0 1 4 4c0 3-4 8-4 8S2 7 2 4a4 4 0 0 1 4-4zm0 2.3a1.7 1.7 0 1 0 0 3.4 1.7 1.7 0 0 0 0-3.4z"/></svg></span>
    </div>
    <div class="address-lines">
      48 Copperleaf Lane, Suite 12<br>
      Westbridge, NY 10452.
    </div>
  </section>

  <section class="card card--back">
    <div class="brand-name">LANTERNFIELD<br>DRINKS</div>
    <div class="website">www.lanternfield.com</div>
  </section>
</body>
</html>
```